Moravel Aesthetic Doctor

I require an elegant, luxurious looking business card for my aesthetic business. I am a doctor and that will set me aside from competitors. I am planning to provide home and spa based treatments to clients with high expectations. I have attached my logo.

```html
<!DOCTYPE html>
<html lang="en">
<head>
<meta charset="utf-8">
<title>Moravel Aesthetic Doctor – Business Card</title>
<link rel="stylesheet" href="https://fonts.googleapis.com/css2?family=Cormorant+Garamond:wght@400&family=Arimo:wght@400;700&display=swap">
<style>
  :root {
    --page-bg: #2a2a2a;
    --card-white: #ffffff;
    --sky: #7ec8ec;
    --brand-grey: #8c8f93;
    --ring-grey: #a7a9ac;
    --ink-white: #ffffff;
    --card-shadow: rgba(0, 0, 0, 0.45);
  }
  * { margin: 0; padding: 0; box-sizing: border-box; }
  html, body {
    width: 1200px;
    height: 1015px;
    overflow: hidden;
    background: var(--page-bg);
  }
  .canvas {
    position: relative;
    width: 1200px;
    height: 1015px;
  }
  .card {
    position: absolute;
    left: 200px;
    width: 800px;
    height: 457px;
    background: var(--card-white);
    overflow: hidden;
    box-shadow: 0 12px 30px var(--card-shadow);
  }
  .card--front { top: 34px; }
  .card--back { top: 524px; }

  /* brand wordmark */
  .wordmark {
    position: absolute;
    display: flex;
    align-items: center;
    gap: 18px;
    font-family: "Cormorant Garamond", serif;
    font-weight: 400;
    color: var(--brand-grey);
  }
  .wordmark__dot {
    width: 58px;
    height: 58px;
    border-radius: 50%;
    border: 3px solid var(--ring-grey);
    flex: none;
  }
  .wordmark__name {
    display: block;
    font-size: 62px;
    line-height: 0.9;
    letter-spacing: 4px;
  }
  .wordmark__role {
    display: block;
    font-size: 23px;
    letter-spacing: 2.5px;
    margin-top: 4px;
  }
  .card--front .wordmark { left: 205px; top: 40px; }

  .photo-strip {
    position: absolute;
    left: 0;
    top: 170px;
    width: 800px;
    height: 287px;
  }

  /* back side */
  .back-art {
    position: absolute;
    inset: 0;
    width: 800px;
    height: 457px;
  }
  .card--back .wordmark { left: 58px; top: 150px; gap: 14px; }
  .card--back .wordmark__dot { width: 48px; height: 48px; }
  .card--back .wordmark__name { font-size: 48px; letter-spacing: 3px; }
  .card--back .wordmark__role { font-size: 18px; letter-spacing: 2px; }
  .tagline {
    position: absolute;
    left: 112px;
    top: 252px;
    font-family: "Arimo", sans-serif;
    font-size: 13px;
    letter-spacing: 1.3px;
    color: var(--brand-grey);
  }
  .details {
    position: absolute;
    right: 40px;
    top: 40px;
    text-align: right;
    font-family: "Arimo", sans-serif;
    color: var(--ink-white);
  }
  .details__name {
    font-size: 28px;
    font-weight: 700;
  }
  .details__post {
    font-size: 14px;
    font-weight: 400;
    letter-spacing: 0.5px;
  }
  .details__diploma {
    font-size: 18px;
    line-height: 1.25;
    margin-top: 6px;
  }
  .social {
    position: absolute;
    right: 40px;
    top: 178px;
    display: flex;
    gap: 8px;
  }
  .social__dot {
    width: 26px;
    height: 26px;
    border-radius: 50%;
    border: 2px solid var(--ink-white);
  }
  .contact {
    position: absolute;
    right: 40px;
    top: 272px;
    list-style: none;
    font-family: "Arimo", sans-serif;
    font-size: 19px;
    color: var(--ink-white);
    text-align: right;
  }
  .contact__item {
    display: flex;
    align-items: center;
    justify-content: flex-end;
    gap: 10px;
    line-height: 30px;
  }
  .contact__icon { width: 18px; height: 18px; flex: none; }
</style>
</head>
<body>
<main class="canvas">

  <!-- Front of card -->
  <section class="card card--front" aria-label="Card front">
    <div class="wordmark">
      <span class="wordmark__dot" aria-hidden="true"></span>
      <span>
        <span class="wordmark__name">MORAVEL</span>
        <span class="wordmark__role">AESTHETIC DOCTOR</span>
      </span>
    </div>

    <svg class="photo-strip" viewBox="0 0 800 287">
      <defs>
        <linearGradient id="tone-massage" x1="0" y1="0" x2="1" y2="1">
          <stop offset="0" stop-color="#7aa7c2"/>
          <stop offset="0.5" stop-color="#b98566"/>
          <stop offset="1" stop-color="#2f6f93"/>
        </linearGradient>
        <linearGradient id="tone-candles" x1="0" y1="0" x2="1" y2="1">
          <stop offset="0" stop-color="#3b2a1e"/>
          <stop offset="0.5" stop-color="#b48a5e"/>
          <stop offset="1" stop-color="#e9a440"/>
        </linearGradient>
        <linearGradient id="tone-products" x1="0" y1="0" x2="1" y2="1">
          <stop offset="0" stop-color="#e9e6e2"/>
          <stop offset="0.6" stop-color="#cfc8bf"/>
          <stop offset="1" stop-color="#8e857b"/>
        </linearGradient>
        <linearGradient id="tone-facial" x1="0" y1="0" x2="1" y2="1">
          <stop offset="0" stop-color="#c9a58c"/>
          <stop offset="0.5" stop-color="#e7b7b6"/>
          <stop offset="1" stop-color="#3c4656"/>
        </linearGradient>
      </defs>
      <polygon role="img" aria-label="Photo: client relaxing during a head and face massage" fill="url(#tone-massage)" points="0,70 208,40 168,287 0,287"/>
      <polygon role="img" aria-label="Photo: rolled towels beside lit spa candles" fill="url(#tone-candles)" points="216,38 410,10 370,287 176,287"/>
      <polygon role="img" aria-label="Photo: skincare serums and botanicals on marble" fill="url(#tone-products)" points="418,9 610,0 572,287 378,287"/>
      <polygon role="img" aria-label="Photo: gloved practitioner giving a facial treatment" fill="url(#tone-facial)" points="618,0 800,0 800,287 580,287"/>
    </svg>
  </section>

  <!-- Back of card -->
  <section class="card card--back" aria-label="Card back">
    <svg class="back-art" viewBox="0 0 800 457" aria-hidden="true">
      <rect width="800" height="457" fill="var(--sky)"/>
      <circle cx="170" cy="300" r="306" fill="none" stroke="var(--ring-grey)" stroke-width="5"/>
      <circle cx="170" cy="300" r="300" fill="var(--card-white)"/>
    </svg>

    <div class="wordmark">
      <span class="wordmark__dot" aria-hidden="true"></span>
      <span>
        <span class="wordmark__name">MORAVEL</span>
        <span class="wordmark__role">AESTHETIC DOCTOR</span>
      </span>
    </div>
    <p class="tagline">HOME AND SPA BASED TREATMENTS</p>

    <div class="details">
      <p class="details__name">Dr Elena Varga <span class="details__post">MRCPCH MD</span></p>
      <p class="details__diploma">Australasian Diploma of<br>Aesthetic Medicine</p>
    </div>

    <div class="social" aria-label="Social profiles">
      <span class="social__dot"></span>
      <span class="social__dot"></span>
    </div>

    <ul class="contact">
      <li class="contact__item">0800 555 014
        <svg class="contact__icon" viewBox="0 0 24 24" aria-hidden="true"><path fill="#fff" d="M6.6 10.8a15.1 15.1 0 0 0 6.6 6.6l2.2-2.2c.3-.3.7-.4 1-.2 1.1.4 2.3.6 3.6.6.6 0 1 .4 1 1V20c0 .6-.4 1-1 1A17 17 0 0 1 3 4c0-.6.4-1 1-1h3.5c.6 0 1 .4 1 1 0 1.3.2 2.5.6 3.6.1.3 0 .7-.2 1z"/></svg>
      </li>
      <li class="contact__item">elena@moravel.co.nz
        <svg class="contact__icon" viewBox="0 0 24 24" aria-hidden="true"><rect x="2" y="5" width="20" height="14" fill="#fff"/><path d="M2 5l10 8 10-8" fill="none" stroke="#7ec8ec" stroke-width="1.8"/></svg>
      </li>
      <li class="contact__item">www.moravel.co.nz
        <svg class="contact__icon" viewBox="0 0 24 24" aria-hidden="true"><g fill="none" stroke="#fff" stroke-width="1.8"><circle cx="12" cy="12" r="9.5"/><ellipse cx="12" cy="12" rx="4" ry="9.5"/><path d="M2.5 12h19M4 7h16M4 17h16"/></g></svg>
      </li>
    </ul>
  </section>

</main>
</body>
</html>
```